Accounting firm needing business card / letterhead designed
Marcus L. Trenholm, CPA
marcus@veltrowledger.com
www.veltrowledger.com
842 E Alder Ave Brinmoor, OH 43827
419-562-0974

```html
<!DOCTYPE html>
<html lang="en">
<head>
<meta charset="utf-8">
<title>Veltrow Ledger – Business Card</title>
<link rel="stylesheet" href="https://fonts.googleapis.com/css2?family=Roboto:wght@400;500&family=Roboto+Condensed:wght@500&display=swap">
<style>
  :root {
    --navy: #241f5c;
    --green: #7fc23a;
    --white: #ffffff;
    --card-stock: #f6f6f4;
    --backdrop: #e4e4e2;
  }
  * { margin: 0; padding: 0; box-sizing: border-box; }
  html, body {
    width: 1200px; height: 960px; overflow: hidden;
    background: var(--backdrop);
    font-family: "Roboto", Arial, sans-serif;
  }
  .canvas { position: relative; width: 1200px; height: 960px; }

  .card { position: absolute; width: 600px; height: 343px; }
  .card--front { left: 314px; top: 113px; background: var(--card-stock); }
  .card--back { left: 311px; top: 472px; background: var(--navy); }

  .accent-bar {
    position: absolute; left: 0; top: 73px;
    width: 16px; height: 195px; background: var(--green);
  }
  .front-brand {
    position: absolute; left: 16px; top: 73px; width: 320px; height: 195px;
    display: flex; align-items: center; justify-content: center;
  }
  .brand-name {
    font-family: "Roboto", Arial, sans-serif;
    font-weight: 500; letter-spacing: 0.04em; text-transform: uppercase;
    white-space: nowrap;
  }
  .front-brand .brand-name { color: var(--navy); font-size: 31px; }

  .contact-panel {
    position: absolute; left: 336px; top: 73px;
    width: 264px; height: 195px; background: var(--navy);
    padding: 26px 0 0 32px; color: var(--white);
  }
  .contact-name {
    font-family: "Roboto Condensed", Arial, sans-serif;
    font-weight: 500; font-size: 21px; line-height: 24px; color: var(--green);
    margin-bottom: 12px;
  }
  .contact-address { font-size: 14px; line-height: 18px; margin-bottom: 11px; }
  .contact-list { list-style: none; font-size: 14px; line-height: 19px; }
  .contact-list li { display: flex; align-items: center; gap: 8px; }
  .contact-list svg { width: 14px; height: 14px; flex: none; }

  .back-brand {
    position: absolute; left: 0; top: 108px; width: 600px;
    text-align: center;
  }
  .back-brand .brand-name { color: var(--white); font-size: 50px; }
  .back-web {
    position: absolute; left: 0; top: 281px; width: 600px;
    text-align: center; color: var(--white);
    font-size: 14px; letter-spacing: 0.42em;
  }
</style>
</head>
<body>
<main class="canvas">
  <section class="card card--front" aria-label="Business card front">
    <div class="accent-bar"></div>
    <div class="front-brand"><span class="brand-name">Veltrow Ledger</span></div>
    <div class="contact-panel">
      <p class="contact-name">Marcus L. Trenholm, CPA</p>
      <p class="contact-address">842 E Alder Ave<br>Brinmoor, OH 43827</p>
      <ul class="contact-list">
        <li>
          <svg viewBox="0 0 24 24" aria-hidden="true"><path fill="#7fc23a" d="M6.6 10.8a15.1 15.1 0 0 0 6.6 6.6l2.2-2.2a1 1 0 0 1 1-.25 11.4 11.4 0 0 0 3.6.57 1 1 0 0 1 1 1V20a1 1 0 0 1-1 1A17 17 0 0 1 3 4a1 1 0 0 1 1-1h3.5a1 1 0 0 1 1 1c0 1.25.2 2.45.57 3.570a1 1 0 0 1-.25 1z"/></svg>
          <span>419-562-0974</span>
        </li>
        <li>
          <svg viewBox="0 0 24 24" aria-hidden="true"><path fill="#7fc23a" d="M2 5h20v14H2z"/><path fill="none" stroke="#241f5c" stroke-width="2" d="M2 5l10 8 10-8"/></svg>
          <span>marcus@veltrowledger.com</span>
        </li>
        <li>
          <svg viewBox="0 0 24 24" aria-hidden="true"><circle cx="12" cy="12" r="10" fill="#7fc23a"/><path fill="none" stroke="#241f5c" stroke-width="1.6" d="M2 12h20M12 2c3 3 3 17 0 20M12 2c-3 3-3 17 0 20"/></svg>
          <span>www.veltrowledger.com</span>
        </li>
      </ul>
    </div>
  </section>

  <section class="card card--back" aria-label="Business card back">
    <div class="back-brand"><span class="brand-name">Veltrow Ledger</span></div>
    <p class="back-web">www.veltrowledger.com</p>
  </section>
</main>
</body>
</html>
```